Bourbon label design for bourbon brand. Looking to freshen our current label.

I need a Bourbon label design for our rebranded Bourbon bottle. Label should include picture of our horse and our logo on the bottle. Front Label is 3.5 inches wide and 6 inches tall, back label is 4 inches tall and 3 inches wide. Back label can be a simple plain logo like the one in the brief. I have included a design of our current bottle and label. We want to stay close to the current color schemes but want a fresh rebrand of the design. The label needs to be the correct size on a tall bottle like pictured.

Target Market(s)

Our Bourbon members, 30-50 year old males

Requirements
Must have
• Picture of our horse, our B logo , straight Bourbon whiskey on the front. Room to edit text on the back label.

```html
<!DOCTYPE html>
<html lang="en">
<head>
<meta charset="utf-8">
<title>Nightfall Straight Bourbon Whiskey – Label Set</title>
<link rel="stylesheet" href="https://fonts.googleapis.com/css2?family=Oswald:wght@500;600;700&family=Source+Sans+3:wght@400&display=swap">
<style>
  :root {
    --board: #c4c4c4;
    --label-paper: #ececec;
    --ink-black: #000000;
    --ink-grey: #9a9a9a;
    --ink-grey-soft: #8f8f8f;
    --ink-white: #ffffff;
    --photo-light: #d2d2d2;
    --photo-dark: #6e6e6e;
  }
  html, body {
    margin: 0;
    padding: 0;
    width: 1000px;
    height: 1200px;
    overflow: hidden;
    background: var(--board);
  }
  .label-board {
    position: relative;
    width: 1000px;
    height: 1200px;
  }
  .label {
    position: absolute;
    background: var(--label-paper);
    overflow: hidden;
  }
  .label svg {
    position: absolute;
    inset: 0;
    width: 100%;
    height: 100%;
    display: block;
  }
  .label--front { left: 83px; top: 78px; width: 329px; height: 564px; }
  .label--back  { left: 107px; top: 744px; width: 285px; height: 377px; }

  .display { font-family: "Oswald", "Arial Narrow", sans-serif; font-weight: 700; }
  .display--medium { font-weight: 500; }
  .fill-black { fill: var(--ink-black); }
  .fill-grey { fill: var(--ink-grey); }
  .fill-grey-soft { fill: var(--ink-grey-soft); }
  .fill-white { fill: var(--ink-white); }
  .band { fill: var(--ink-black); }

  .story {
    position: absolute;
    left: 24px;
    top: 44px;
    width: 172px;
    margin: 0;
    font-family: "Source Sans 3", "Helvetica Neue", sans-serif;
    font-size: 10.2px;
    line-height: 13.3px;
    color: var(--ink-black);
  }
  .story p { margin: 0 0 13.3px 0; }
</style>
</head>
<body>
<main class="label-board">

  <!-- Front label -->
  <section class="label label--front" aria-label="Front label">
    <svg viewBox="0 0 329 564" xmlns="http://www.w3.org/2000/svg">
      <defs>
        <linearGradient id="horse-tone" x1="0" y1="0" x2="0" y2="1">
          <stop offset="0" stop-color="var(--photo-dark)"/>
          <stop offset="0.6" stop-color="#8a8a8a"/>
          <stop offset="1" stop-color="var(--photo-light)"/>
        </linearGradient>
      </defs>

      <path class="band" d="M191,0 H329 V545 H294 A40,40 0 0 1 254,505 V63 A63,63 0 0 0 191,0 Z"/>

      <g class="title">
        <text class="display fill-black" x="27" y="96" font-size="48" textLength="207" lengthAdjust="spacingAndGlyphs">NIGHTFALL</text>
        <text class="display fill-grey" x="27" y="145" font-size="48" textLength="207" lengthAdjust="spacingAndGlyphs">STRAIGHT</text>
        <text class="display fill-grey" x="27" y="194" font-size="48" textLength="202" lengthAdjust="spacingAndGlyphs">BOURBON</text>
        <text class="display fill-grey" x="27" y="242" font-size="48" textLength="200" lengthAdjust="spacingAndGlyphs">WHISKEY</text>
      </g>

      <g class="established">
        <text class="display display--medium fill-white" x="268" y="74" font-size="12" textLength="47" lengthAdjust="spacingAndGlyphs">EST. 2016</text>
        <rect class="fill-white" x="268" y="80" width="47" height="1"/>
      </g>

      <g class="cask-notes">
        <text class="display display--medium fill-grey-soft" x="29" y="301" font-size="13">SINGLE</text>
        <text class="display display--medium fill-grey-soft" x="29" y="318" font-size="13">BARREL</text>
        <rect class="fill-grey-soft" x="29" y="322" width="23" height="3"/>
        <text class="display display--medium fill-grey-soft" x="29" y="363" font-size="13">BARREL</text>
        <text class="display display--medium fill-grey-soft" x="29" y="380" font-size="13">STRENGTH</text>
        <rect class="fill-grey-soft" x="29" y="385" width="23" height="3"/>
      </g>

      <rect class="horse-photo" x="153" y="274" width="121" height="240" rx="50" fill="url(#horse-tone)"
            role="img" aria-label="Black and white photograph of the brand's racehorse galloping toward the viewer with its jockey"/>

      <g class="bottling-fields">
        <text class="display display--medium fill-grey-soft" x="30" y="526" font-size="8.5">BARREL NO.</text>
        <rect class="fill-grey-soft" x="29" y="531" width="60" height="1"/>
        <text class="display display--medium fill-grey-soft" x="98" y="526" font-size="8.5">AGED/YEARS</text>
        <rect class="fill-grey-soft" x="97" y="531" width="59" height="1"/>
        <text class="display display--medium fill-grey-soft" x="167" y="526" font-size="8.5">ALC./VOL.</text>
        <rect class="fill-grey-soft" x="166" y="531" width="60" height="1"/>
      </g>

      <text class="brand-mark display fill-white" x="292" y="508" font-size="10" text-anchor="middle">NIGHTFALL</text>
    </svg>
  </section>

  <!-- Back label -->
  <section class="label label--back" aria-label="Back label">
    <svg viewBox="0 0 285 377" xmlns="http://www.w3.org/2000/svg">
      <path class="band" d="M156,0 H285 V358 H235 A23,23 0 0 1 212,335 V56 A56,56 0 0 0 156,0 Z"/>

      <g class="title-stack">
        <text class="display fill-white" x="222" y="59" font-size="13" textLength="53" lengthAdjust="spacingAndGlyphs">NIGHTFALL</text>
        <text class="display fill-grey" x="222" y="71.5" font-size="13" textLength="52" lengthAdjust="spacingAndGlyphs">STRAIGHT</text>
        <text class="display fill-grey" x="222" y="84" font-size="13" textLength="51" lengthAdjust="spacingAndGlyphs">BOURBON</text>
        <text class="display fill-grey" x="222" y="96.5" font-size="13" textLength="50" lengthAdjust="spacingAndGlyphs">WHISKEY</text>
      </g>

      <g class="established">
        <text class="display display--medium fill-white" x="235" y="330" font-size="10" textLength="36" lengthAdjust="spacingAndGlyphs">EST. 2016</text>
        <rect class="fill-white" x="235" y="335" width="36" height="1"/>
      </g>

      <text class="brand-mark display fill-black" x="26" y="325" font-size="11">NIGHTFALL</text>
    </svg>

    <div class="story">
      <p>Lorem ipsum dolor sit amet, consectetur adipiscing elit. Quisque placerat sem at nunc venenatis venenatis. Vestibulum dapibus dui lectus, non accumsan mauris tincidunt et. In non viverra turpis.</p>
      <p>Aenean id finibus magna, et feugiat ipsum. Proin laoreet gravida lorem nec porta. Suspendisse a neque dictum, tempus lorem ac, suscipit dolor. Fusce id eleifend dolor. Quisque rhoncus sem vel tortor dapibus accumsan.</p>
    </div>
  </section>

</main>
</body>
</html>
```